Mindfulness School for Children -- Business Cards

We're looking for business cards for our school directors and owners. We're a mindfulness school for children called little lanterns. Attached are our logos/icons.

```html
<!DOCTYPE html>
<html lang="en">
<head>
<meta charset="utf-8">
<title>little lanterns — business cards</title>
<link rel="stylesheet" href="https://fonts.googleapis.com/css2?family=Lora:wght@400&family=Work+Sans:wght@400;600&display=swap">
<style>
  :root {
    --backdrop: #e6e3df;
    --card-white: #ffffff;
    --teal: #3aa3bf;
    --teal-deep: #1e6f9a;
    --aqua: #45e3f5;
    --green: #8fcf9a;
    --green-text: #7cc38c;
    --ink: #4a4d50;
    --rule: #d9dcde;
    --lotus-wash: #e3f1f6;
  }
  * { box-sizing: border-box; margin: 0; padding: 0; }
  html, body { width: 1200px; height: 997px; overflow: hidden; }
  body {
    background: var(--backdrop);
    font-family: "Work Sans", sans-serif;
    position: relative;
  }
  .card {
    position: absolute;
    left: 290px;
    width: 620px;
    height: 354px;
    border-radius: 3px;
    overflow: hidden;
    box-shadow: 0 10px 26px rgba(0,0,0,0.14);
  }
  /* back side */
  .card-back { top: 105px; }
  .card-back .pattern-fill {
    position: absolute; inset: 0;
    background: linear-gradient(200deg, var(--teal-deep) 0%, #2a8fb3 45%, #2fb4cf 75%, var(--aqua) 100%);
  }
  .card-back .mark-dot {
    position: absolute; right: 92px; top: 150px;
    width: 44px; height: 44px; border-radius: 50%;
    background: rgba(255,255,255,0.8);
  }
  /* front side */
  .card-front { top: 535px; background: var(--card-white); }
  .lotus-wash {
    position: absolute; left: 50px; top: 40px;
    width: 250px; height: 250px;
    border-radius: 50% 50% 46% 46%;
    background: radial-gradient(circle at 50% 45%, var(--lotus-wash) 0%, #edf6f9 60%, rgba(255,255,255,0) 75%);
  }
  .wordmark {
    position: absolute; left: 58px; top: 150px;
    font-family: "Lora", serif;
    font-size: 36px;
    color: var(--teal);
    display: flex; align-items: center; gap: 10px;
  }
  .wordmark .dot { width: 12px; height: 12px; border-radius: 50%; background: var(--teal); }
  .divider {
    position: absolute; left: 342px; top: 40px;
    width: 1px; height: 240px; background: var(--rule);
  }
  .contact { position: absolute; left: 368px; top: 48px; color: var(--ink); }
  .contact .name {
    font-weight: 600; font-size: 17px; letter-spacing: 1px;
    color: var(--teal); text-transform: uppercase;
  }
  .contact .role { font-size: 12px; color: var(--green-text); margin-bottom: 12px; }
  .contact .address { font-size: 12px; line-height: 17px; margin-bottom: 10px; }
  .contact ul { list-style: none; font-size: 12px; line-height: 17px; }
  .contact li { display: flex; align-items: center; gap: 8px; }
  .contact svg { width: 10px; height: 10px; flex: none; }
  .stripe { position: absolute; bottom: 0; height: 9px; }
  .stripe-green { left: 0; width: 390px; background: var(--green); }
  .stripe-teal { left: 394px; right: 0; background: var(--teal); }
</style>
</head>
<body>

<section class="card card-back">
  <div class="pattern-fill" role="img" aria-label="Repeating lotus flower pattern in teal and aqua tones"></div>
  <div class="mark-dot"></div>
</section>

<section class="card card-front">
  <div class="lotus-wash" role="img" aria-label="Large faint lotus decoration"></div>
  <div class="wordmark"><span class="dot"></span>little lanterns</div>
  <div class="divider"></div>
  <div class="contact">
    <p class="name">Daniel Reyes</p>
    <p class="role">President</p>
    <p class="address">412 Willow Bend Road<br>Fairbanks, Alaska 99701</p>
    <ul>
      <li><svg viewBox="0 0 10 10"><path d="M2 1 L4 3 L3 4 Q4 6 6 7 L7 6 L9 8 L7.5 9.5 Q1 8 .5 2.5 Z" fill="#3aa3bf"/></svg>555-210-4816</li>
      <li><svg viewBox="0 0 10 10"><rect x="2.5" y="0.5" width="5" height="9" rx="1" fill="none" stroke="#3aa3bf" stroke-width="1.2"/></svg>555-318-2690</li>
      <li><svg viewBox="0 0 10 10"><rect x="1" y="3" width="8" height="5" fill="#3aa3bf"/><rect x="3" y="1" width="4" height="2" fill="#3aa3bf"/></svg>555-407-7731</li>
      <li><svg viewBox="0 0 10 10"><rect x="0.5" y="2" width="9" height="6.5" fill="#3aa3bf"/><path d="M0.5 2 L5 6 L9.5 2" stroke="#fff" fill="none"/></svg>name@littlelanterns.com</li>
      <li><svg viewBox="0 0 10 10"><circle cx="5" cy="5" r="4.5" fill="#3aa3bf"/><path d="M0.5 5 H9.5 M5 0.5 V9.5" stroke="#fff" stroke-width="0.8"/></svg>www.littlelanterns.com</li>
    </ul>
  </div>
  <div class="stripe stripe-green"></div>
  <div class="stripe stripe-teal"></div>
</section>

</body>
</html>
```